Residential Remodeling Contractor needs updated business card

I need a new design for my business card.
Name of the company is Ridgefell Construction. I need a card that commands presence, strength, integrity. I have been in business for 28 years. I am a Residential Remodeling Contractor that covers all aspects of a residential remodel and build.

```html
<!DOCTYPE html>
<html lang="en">
<head>
<meta charset="utf-8">
<title>Ridgefell Construction – Business Card</title>
<link href="https://fonts.googleapis.com/css2?family=Montserrat:wght@400;500;700&display=swap" rel="stylesheet">
<style>
  :root {
    --navy: #1f3c7f;
    --navy-deep: #18306a;
    --navy-soft: #2e55a8;
    --ink: #1d1d22;
    --paper: #ffffff;
    --stage: #e4e6ea;
  }
  * { box-sizing: border-box; margin: 0; padding: 0; }
  html, body { width: 1200px; height: 900px; overflow: hidden; }
  body {
    background: var(--stage);
    font-family: "Montserrat", Arial, sans-serif;
    position: relative;
  }
  .card {
    position: absolute;
    left: 240px;
    width: 720px;
    height: 411px;
    box-shadow: 0 6px 18px rgba(0,0,0,0.18);
  }
  /* Back side */
  .card-back {
    top: 26px;
    background: var(--navy);
    display: flex;
    align-items: center;
    justify-content: center;
  }
  .card-back .wordmark {
    display: flex;
    align-items: center;
    gap: 16px;
    color: var(--navy-soft);
    font-weight: 700;
    font-size: 40px;
    letter-spacing: 2px;
    text-transform: uppercase;
    line-height: 1.1;
  }
  .card-back .wordmark-square {
    width: 34px; height: 34px;
    background: var(--navy-deep);
    flex: none;
  }
  /* Front side */
  .card-front {
    top: 463px;
    background: var(--paper);
  }
  .brand {
    position: absolute;
    left: 44px; top: 52px;
    display: flex;
    align-items: center;
    gap: 12px;
    color: var(--navy);
    font-weight: 700;
    font-size: 27px;
    letter-spacing: 1.5px;
    text-transform: uppercase;
    line-height: 1.1;
  }
  .brand-square {
    width: 22px; height: 22px;
    background: var(--navy);
    flex: none;
  }
  .person {
    position: absolute;
    right: 44px; top: 52px;
    text-align: right;
  }
  .person-name {
    color: var(--navy);
    font-weight: 700;
    font-size: 27px;
    letter-spacing: 1.5px;
    text-transform: uppercase;
  }
  .person-title {
    color: var(--ink);
    font-size: 15px;
    margin-top: 2px;
  }
  .contacts {
    position: absolute;
    left: 44px; bottom: 56px;
    list-style: none;
    color: var(--ink);
    font-size: 18px;
    line-height: 1.35;
  }
  .contacts li { display: flex; align-items: center; gap: 6px; }
  .contacts svg { width: 15px; height: 15px; flex: none; }
  .contacts .web-name { color: var(--navy); }
  .address {
    position: absolute;
    right: 44px; bottom: 56px;
    color: var(--ink);
    font-size: 18px;
    line-height: 1.35;
    font-style: normal;
    letter-spacing: 0.5px;
  }
</style>
</head>
<body>

<section class="card card-back">
  <div class="wordmark">
    <span class="wordmark-square"></span>
    <span>Ridgefell<br>Construction</span>
  </div>
</section>

<section class="card card-front">
  <div class="brand">
    <span class="brand-square"></span>
    <span>Ridgefell<br>Construction</span>
  </div>

  <div class="person">
    <div class="person-name">Marcus Delaney</div>
    <div class="person-title">Director</div>
  </div>

  <ul class="contacts">
    <li>
      <svg viewBox="0 0 16 16" aria-hidden="true"><path d="M4 1.5l2.2 3-1.3 1.6c.8 1.9 2.2 3.4 4.1 4.3l1.6-1.3 3 2.2-1.1 2.6C7.5 13.6 2.4 8.5 1.4 3z" fill="#1f3c7f"/></svg>
      (555) 218-4470
    </li>
    <li>
      <svg viewBox="0 0 16 16" aria-hidden="true"><rect x="1.5" y="3.5" width="13" height="9" fill="none" stroke="#1f3c7f" stroke-width="1.4"/><path d="M1.5 3.5l6.5 5 6.5-5" fill="none" stroke="#1f3c7f" stroke-width="1.4"/></svg>
      info@ridgefellbuild.com
    </li>
    <li>
      <svg viewBox="0 0 16 16" aria-hidden="true"><circle cx="8" cy="8" r="6.5" fill="none" stroke="#1f3c7f" stroke-width="1.3"/><ellipse cx="8" cy="8" rx="2.8" ry="6.5" fill="none" stroke="#1f3c7f" stroke-width="1.1"/><path d="M1.5 8h13M2.5 5h11M2.5 11h11" stroke="#1f3c7f" stroke-width="1"/></svg>
      <span>www.<span class="web-name">ridgefellbuild</span>.com</span>
    </li>
  </ul>

  <address class="address">
    742 Harlow Street<br>
    Dunmore, GA 30999
  </address>
</section>

</body>
</html>
```